New, modern business card for growing audiology practice

We need a new business card for our audiology practice. Our logo and website have recently changed (more modern) and we want our business cards to reflect this change.
We conduct hearing tests, perform earwax removals, and fit & dispense hearing aids to our patients. We are a family owned practice in which the owner is the one who works directly with the patient. I have attached logos in various formats to use, as well as two ideas I found on this website; as well as a scanned copy of our current logo. Good luck!

Industry/Entity Type

Business

Contact Information for Business Card

Company name: Tolvera Hearing Center
Provider name: Peter Wolstenby, Au.D. F/NSB
Phone number: (440) 683-5127
Address: 837 W. Lindell Ave. Marlow Heights, OH 44187
email: tolverahearing@postvane.com
website: tolverahearing.com

Colors
000000
aaaaaa
dbdbdb
cacaca
9bcb3c
afd23c
cadf82
b1b1b1

Requirements
Must have
• My card must include information in the "details" section. In the attached images, I found a few that I liked and I would like to model after - "brisky bouncin'" and "Sound Method Center".
• Must be horizontal.
• Must include logos provided. I uploaded them in various file formats and various ways.
• Must match logo font, if possible, if not, please get as close as you can.
Nice to have
• I really like the idea of having a color on one side with just the logo and company name and the contact information and provider name on the other side. I also really like the idea of having the main color dominating on the logo/company side with accent of that same color on the contact side of the card.
Should not have
• Must not be vertical.

```html
<!DOCTYPE html>
<html lang="en">
<head>
<meta charset="utf-8">
<title>Tolvera Hearing Center – Business Card</title>
<link href="https://fonts.googleapis.com/css2?family=Lato:wght@400&family=Roboto:wght@400;500&family=Roboto+Condensed:wght@700&display=swap" rel="stylesheet">
<style>
  :root {
    --backdrop: #e9e6e1;
    --card-dark: #1a1b1d;
    --card-light: #f3f3f3;
    --brand-green: #76a136;
    --ink: #111111;
    --white: #ffffff;
  }
  html, body {
    margin: 0;
    width: 1200px;
    height: 960px;
    overflow: hidden;
    background: var(--backdrop);
  }
  .canvas { position: relative; width: 1200px; height: 960px; }

  .card {
    position: absolute;
    width: 600px;
    height: 342px;
    border-radius: 18px;
    overflow: hidden;
    box-shadow: 0 2px 6px rgba(0,0,0,.25);
  }

  /* Front: brand side */
  .card--front { left: 322px; top: 110px; background: var(--card-dark); }
  .card--front .wordmark {
    position: absolute; left: 0; right: 0; top: 152px;
    text-align: center;
    font: 400 29px/1 "Lato", sans-serif;
    color: var(--white);
    letter-spacing: .2px;
  }
  .card--front .wordmark .mark-dot {
    display: inline-block; width: 14px; height: 14px; border-radius: 50%;
    background: var(--brand-green); margin-right: 12px; vertical-align: 2px;
  }
  .card--front .web {
    position: absolute; left: 0; right: 0; top: 284px;
    text-align: center;
    font: 400 14px/1 "Roboto", sans-serif;
    letter-spacing: 3.2px;
    color: var(--white);
  }

  /* Back: contact side */
  .card--back { left: 320px; top: 493px; background: var(--card-light); }
  .card--back .wordmark {
    position: absolute; left: 35px; top: 45px;
    font: 400 21px/1 "Lato", sans-serif;
    color: var(--ink);
  }
  .card--back .wordmark .mark-dot {
    display: inline-block; width: 11px; height: 11px; border-radius: 50%;
    background: var(--brand-green); margin-right: 9px; vertical-align: 1px;
  }
  .provider { position: absolute; left: 68px; top: 94px; }
  .provider__name {
    font: 700 21px/1 "Roboto Condensed", sans-serif;
    color: var(--brand-green);
    text-transform: uppercase;
    margin: 0;
  }
  .provider__title {
    font: 500 14px/1 "Roboto", sans-serif;
    color: var(--ink);
    margin: 8px 0 0;
  }
  .swoosh { position: absolute; left: 0; top: 0; width: 600px; height: 342px; }
  .contact {
    position: absolute; left: 35px; top: 220px;
    font: 400 14.5px/19px "Roboto", sans-serif;
    color: var(--white);
  }
  .contact p { margin: 0; }
  .contact__lines { margin-top: 10px; }
  .contact__lines p { display: flex; align-items: center; gap: 9px; }
  .contact__lines svg { width: 13px; height: 13px; fill: var(--white); flex: none; }
</style>
</head>
<body>
<div class="canvas">

  <section class="card card--front">
    <div class="wordmark"><span class="mark-dot"></span>TOLVERA HEARING CENTER</div>
    <div class="web">www.tolverahearing.com</div>
  </section>

  <section class="card card--back">
    <svg class="swoosh" viewBox="0 0 600 342" aria-hidden="true">
      <path d="M0,218 C120,196 320,192 600,316 L600,342 L0,342 Z" fill="#000"/>
      <path d="M0,222 C130,202 340,206 600,342 L0,342 Z" fill="var(--brand-green)"/>
    </svg>

    <div class="wordmark"><span class="mark-dot"></span>TOLVERA HEARING CENTER</div>

    <div class="provider">
      <h1 class="provider__name">Peter Wolstenby</h1>
      <p class="provider__title">AU.D. F/NSB</p>
    </div>

    <div class="contact">
      <p>837 W. Lindell Ave.</p>
      <p>Marlow Heights, OH 44187</p>
      <div class="contact__lines">
        <p><svg viewBox="0 0 24 24"><path d="M6.6 10.8a15.1 15.1 0 0 0 6.6 6.6l2.2-2.2a1 1 0 0 1 1-.25 11.4 11.4 0 0 0 3.6.57 1 1 0 0 1 1 1V20a1 1 0 0 1-1 1A17 17 0 0 1 3 4a1 1 0 0 1 1-1h3.5a1 1 0 0 1 1 1c0 1.25.2 2.45.57 3.57a1 1 0 0 1-.25 1z"/></svg>(440) 683-5127</p>
        <p><svg viewBox="0 0 24 24"><path d="M2 5h20L12 12z"/><path d="M2 7l10 7 10-7v12H2z"/></svg>tolverahearing@postvane.com</p>
        <p><svg viewBox="0 0 24 24"><circle cx="12" cy="12" r="10"/><path d="M2 12h20M12 2c3 3 3 17 0 20M12 2c-3 3-3 17 0 20" stroke="var(--brand-green)" stroke-width="1.6" fill="none"/></svg>tolverahearing.com</p>
      </div>
    </div>
  </section>

</div>
</body>
</html>
```